MRT Property - Business Cards

Looking for a business card & general letterhead, signage etc design for our new logo.

Colours:
000a20
0056a2
00b5ef
0088ce
68cef2

Fonts:
Poppins
Karla

Please keep look and feel of new brand - example in the zip package I sent.

```html
<!DOCTYPE html>
<html lang="en">
<head>
<meta charset="utf-8">
<title>MRT Property – Business Cards</title>
<link rel="stylesheet" href="https://fonts.googleapis.com/css2?family=Poppins:wght@400;600;700&family=Karla:wght@400;500&display=swap">
<style>
  :root {
    --ink: #000a20;
    --brand-blue: #0056a2;
    --sky: #00b5ef;
    --mid-blue: #0088ce;
    --pale-blue: #68cef2;
    --paper: #ffffff;
    --backdrop: #d1d1cd;
    --muted: #3a3f4a;
  }
  * { box-sizing: border-box; margin: 0; padding: 0; }
  html, body { width: 1200px; height: 801px; overflow: hidden; }
  body {
    background: var(--backdrop);
    font-family: "Karla", sans-serif;
    color: var(--ink);
    position: relative;
  }
  .card {
    position: absolute;
    top: 252px;
    width: 520px;
    height: 297px;
    border-bottom: 4px solid var(--sky);
    overflow: hidden;
  }
  .card--front { left: 50px; background: var(--paper); }
  .card--back { left: 630px; background: var(--brand-blue); }

  .wordmark {
    position: absolute;
    font-family: "Poppins", sans-serif;
    font-weight: 700;
    letter-spacing: 0.5px;
    white-space: nowrap;
  }
  .card--front .wordmark { left: 36px; top: 34px; font-size: 34px; color: var(--brand-blue); }
  .card--back .wordmark { right: 40px; top: 150px; font-size: 28px; color: var(--paper); }

  .person { position: absolute; left: 38px; top: 100px; }
  .person__name {
    font-family: "Poppins", sans-serif;
    font-weight: 700;
    font-size: 21px;
    line-height: 1.1;
    color: var(--brand-blue);
  }
  .person__name .surname { color: var(--mid-blue); }
  .person__title { font-size: 13px; color: var(--muted); margin-top: 2px; }

  .divider {
    position: absolute;
    left: 38px; right: 30px; top: 172px;
    height: 1px;
    background: var(--mid-blue);
  }

  .contacts {
    position: absolute;
    left: 38px; top: 190px;
    list-style: none;
    font-family: "Poppins", sans-serif;
    font-size: 13px;
    line-height: 21px;
    color: var(--ink);
  }
  .contacts li { display: flex; align-items: center; gap: 6px; }
  .contacts svg { width: 10px; height: 10px; fill: var(--brand-blue); flex: none; }

  .address {
    position: absolute;
    right: 30px; top: 196px;
    text-align: right;
    font-family: "Poppins", sans-serif;
    font-size: 12.5px;
    line-height: 19px;
    color: var(--ink);
  }

  .back-pattern {
    position: absolute;
    inset: 0;
    background: linear-gradient(120deg, #0a3f7a 0%, var(--brand-blue) 45%, var(--mid-blue) 100%);
  }
</style>
</head>
<body>

  <section class="card card--front" aria-label="Business card front">
    <div class="wordmark">MRT Property</div>

    <div class="person">
      <div class="person__name">DANA <span class="surname">ELLIS</span></div>
      <div class="person__title">Founder &amp; Principal</div>
    </div>

    <div class="divider"></div>

    <ul class="contacts">
      <li>
        <svg viewBox="0 0 10 10" aria-hidden="true"><path d="M2 0.5 L3.6 0.5 L4.2 3 L3 3.8 Q4 6 6.2 7 L7 5.8 L9.5 6.4 L9.5 8 Q9.5 9.5 8 9.5 Q1 9 0.5 2 Q0.5 0.5 2 0.5 Z"/></svg>
        +1- 555-014-2290
      </li>
      <li>
        <svg viewBox="0 0 10 10" aria-hidden="true"><path d="M0.5 2 H9.5 V8 H0.5 Z M1.5 3 V7 H8.5 V3 L5 5.6 Z" fill-rule="evenodd"/></svg>
        info@mrtproperty.com
      </li>
      <li>
        <svg viewBox="0 0 10 10" aria-hidden="true"><circle cx="5" cy="5" r="4.5"/></svg>
        www.mrtproperty.com
      </li>
    </ul>

    <div class="address">
      2470 Harbor View Road<br>
      #18, Suite Lakeside
    </div>
  </section>

  <section class="card card--back" aria-label="Business card back">
    <div class="back-pattern" role="img" aria-label="Repeating brand pattern in shades of blue"></div>
    <div class="wordmark">MRT Property</div>
  </section>

</body>
</html>
```